Modern Business Card

Modern professional business card with more than just logo and demographic info. Something memorable.

We are a trendy/modern chiropractic group with an emphasis on neurology, hence the minimalist-type brain logo. We want to convey that modern and technical aspect with professionalism and the elite nature of our practice environment.

```html
<!DOCTYPE html>
<html lang="en">
<head>
<meta charset="UTF-8">
<title>Cadence Chiropractic – Business Card</title>
<link rel="stylesheet" href="https://fonts.googleapis.com/css2?family=Open+Sans:wght@400;700&display=swap">
<style>
  :root {
    --brand-blue: #4780c0;
    --ink: #111111;
    --muted: #555555;
    --paper: #ffffff;
    --page: #ffffff;
    --shadow: rgba(0, 0, 0, 0.14);
  }
  * { box-sizing: border-box; margin: 0; padding: 0; }
  html, body {
    width: 1200px;
    height: 1200px;
    overflow: hidden;
    background: var(--page);
    font-family: "Open Sans", Arial, sans-serif;
  }
  .canvas { position: relative; width: 1200px; height: 1200px; }

  .card {
    position: absolute;
    left: 115px;
    width: 970px;
    height: 554px;
    overflow: hidden;
    box-shadow: 0 2px 10px var(--shadow);
  }

  /* Front side */
  .card-front { top: 42px; background: var(--brand-blue); }
  .front-brand {
    position: absolute;
    left: 0; right: 0; top: 0; bottom: 0;
    display: flex;
    flex-direction: column;
    align-items: center;
    justify-content: center;
    gap: 22px;
    color: var(--paper);
  }
  .front-brand .brand-square {
    width: 64px; height: 64px;
    background: var(--paper);
  }
  .front-brand .brand-name {
    font-size: 42px;
    font-weight: 400;
    letter-spacing: 3px;
    line-height: 1.15;
    text-align: center;
    text-transform: uppercase;
  }

  /* Back side */
  .card-back { top: 605px; background: var(--paper); }
  .back-brand {
    position: absolute;
    left: 47px; top: 40px;
    display: flex;
    align-items: center;
    gap: 18px;
    color: var(--brand-blue);
  }
  .back-brand .brand-square {
    width: 72px; height: 72px;
    background: var(--brand-blue);
  }
  .back-brand .brand-name {
    font-size: 34px;
    font-weight: 400;
    letter-spacing: 2px;
    line-height: 1.15;
    text-transform: uppercase;
  }

  .person { position: absolute; left: 47px; top: 220px; }
  .person-name {
    font-size: 34px;
    font-weight: 700;
    color: var(--ink);
    letter-spacing: 0.5px;
    line-height: 1.2;
  }
  .person-role {
    font-size: 25px;
    color: var(--muted);
    line-height: 1.25;
  }

  .address {
    position: absolute;
    left: 47px; top: 322px;
    font-size: 25px;
    line-height: 35px;
    color: var(--muted);
  }

  .contacts {
    position: absolute;
    left: 47px; top: 408px;
    list-style: none;
  }
  .contacts li {
    display: flex;
    align-items: center;
    gap: 18px;
    height: 36px;
    font-size: 25px;
    color: var(--muted);
  }
  .contacts svg { width: 24px; height: 24px; fill: var(--brand-blue); flex: none; }

  .accent-shape {
    position: absolute;
    left: 690px; top: 130px;
    width: 340px; height: 340px;
    border-radius: 50%;
    background: var(--brand-blue);
  }
</style>
</head>
<body>
<main class="canvas">

  <section class="card card-front" aria-label="Card front">
    <div class="front-brand">
      <span class="brand-square"></span>
      <p class="brand-name">Cadence<br>Chiropractic</p>
    </div>
  </section>

  <section class="card card-back" aria-label="Card back">
    <div class="back-brand">
      <span class="brand-square"></span>
      <p class="brand-name">Cadence<br>Chiropractic</p>
    </div>

    <div class="person">
      <h1 class="person-name">DANIEL REYES</h1>
      <p class="person-role">President</p>
    </div>

    <address class="address" style="font-style:normal">
      Street Name Here, Suite 100<br>
      Street Zip Code,Country
    </address>

    <ul class="contacts">
      <li>
        <svg viewBox="0 0 24 24" aria-hidden="true"><path d="M6.6 10.8a15.1 15.1 0 0 0 6.6 6.6l2.2-2.2a1 1 0 0 1 1-.25 11.4 11.4 0 0 0 3.6.6 1 1 0 0 1 1 1V20a1 1 0 0 1-1 1A17 17 0 0 1 3 4a1 1 0 0 1 1-1h3.5a1 1 0 0 1 1 1c0 1.25.2 2.45.6 3.6a1 1 0 0 1-.25 1z"/></svg>
        01234-56789
      </li>
      <li>
        <svg viewBox="0 0 24 24" aria-hidden="true"><path d="M2 5h20v14H2z" fill="none"/><path d="M2 6v12h20V6zm2 1.5 8 6 8-6V17H4z"/></svg>
        info@yourwebsite.com
      </li>
      <li>
        <svg viewBox="0 0 24 24" aria-hidden="true"><path d="M12 2a10 10 0 1 0 0 20 10 10 0 0 0 0-20zm6.9 6h-3a15 15 0 0 0-1.3-4 8 8 0 0 1 4.3 4zM12 4c.8 1.2 1.5 2.5 1.9 4h-3.8c.4-1.5 1.1-2.8 1.9-4zM4.3 14a8 8 0 0 1 0-4h3.4a16 16 0 0 0 0 4zm.8 2h3a15 15 0 0 0 1.3 4 8 8 0 0 1-4.3-4zm3-8h-3a8 8 0 0 1 4.3-4 15 15 0 0 0-1.3 4zM12 20c-.8-1.2-1.5-2.5-1.9-4h3.8c-.4 1.5-1.1 2.8-1.9 4zm2.3-6H9.7a14 14 0 0 1 0-4h4.6a14 14 0 0 1 0 4zm.3 6a15 15 0 0 0 1.3-4h3a8 8 0 0 1-4.3 4zm1.7-6a16 16 0 0 0 0-4h3.4a8 8 0 0 1 0 4z"/></svg>
        www.yourwebsite.com
      </li>
    </ul>

    <span class="accent-shape" aria-hidden="true"></span>
  </section>

</main>
</body>
</html>
```